Web Design for Webdesign company 3 page PSD

Project
---------
We need a PSD Web Design to be used in a WordPress installation.
What we would like to create is a professional looking website for a web design agency. We also need you to look for suitable stock images to be placed on these pages.
We need the design for:
Homepage
Landing page
Contact page
attached in the pages file you will find a file with more in depth details how these files should be build up.
We would like to see a desktop version and a mobile version of these pages
The website should have a 1100px width.
The mobile design should have 480px width.
The homepage should have a header slider about 450px high.
The slider is preferred full width and should have some images text and a button
Objectives
-------------
The main objective for the website is to get leads from customers in the form of a request for a quotation or a call or mail me back action. The most important action for the homepage is to link and navigate to our landing pages.
What we want to tell our visitors (our main products)
-------------------------------------------------------------------
- A website with no big investment but a monthly rate
- A successful website with no worries (a complete website, seo, hosting and a service contract for future customization is included for a monthly rate)
Color Scheme
------------
Use branding colors. You can find them in the branding.pdf file.
Additional colors:
White: #ffffff
Black: #181818
Company info
--------------
We are a starting web design / marketing agency based in The Netherlands and looking for the design of our website. Our services are (custom) webdesign, website marketing or combinations of both. Our main customer group is small business owners.
We sell websites but give the option to buy it with a lease contract.
A second product is a default website with a complete service: SEO, hosting and a service contract for a monthly rate.
Content:
-----------
If not available place Lorem Ipsum text.
There will come about 400 words of text on the landing pages
Design Competition
--------------------------
Since this is a designing competition we would like to see your creativity.
What you can expect from us is a lot of feedback 7 days a week with short response time.
You can send us the first sketchy mock ups of the homepage and we will give feedback based on these design. But we like your feedback or comments as well
Read the pages file for more in depth details how the pages should be designed

Target Market(s)
Small business owners in The Netherlands
Industry/Entity Type
It Company
Number of Pages Required
3 page
Requirements
Must have
- Homepage:
- Header slider with images, some text and a link to a custom page
- The slider should have 3 designed slides
- Landings page:
- Sidebar
- Action button for a request for a quotation
- Action button for a call me back action
- Action button for an appointment
- Contact form:
- Address details
- Contact form
Nice to have
- Homepage:
- Full width slider
- Testimonial block
- Blog items
Should not have
- Flash
- A to crowded design

```html
<!DOCTYPE html>
<html lang="en">
<head>
<meta charset="utf-8">
<title>Oakline Web Studio</title>
<link rel="stylesheet" href="https://fonts.googleapis.com/css2?family=Open+Sans:wght@400;600&family=Raleway:wght@400;500&display=swap">
<style>
  :root {
    --teal: #1b6f7c;
    --teal-deep: #15606c;
    --teal-hero: #207a87;
    --yellow: #f9c80e;
    --ink: #181818;
    --text: #333333;
    --muted: #6e6e6e;
    --line: #c9c9c9;
    --white: #ffffff;
  }
  * { box-sizing: border-box; margin: 0; padding: 0; }
  html, body { width: 1200px; height: 980px; overflow: hidden; background: var(--white); }
  body { position: relative; font-family: "Open Sans", Arial, sans-serif; color: var(--text); }

  .site-header { position: absolute; top: 0; left: 0; width: 1200px; height: 97px; border-bottom: 1px solid #d7d7d7; background: var(--white); }
  .brand { position: absolute; left: 215px; top: 26px; display: flex; align-items: center; gap: 12px; }
  .brand-mark { width: 40px; height: 40px; border-radius: 50%; background: var(--teal); }
  .brand-text { font-family: "Raleway", Arial, sans-serif; font-weight: 500; color: var(--teal); line-height: 1.15; }
  .brand-name { font-size: 20px; }
  .brand-tagline { font-size: 11px; }
  .support { position: absolute; right: 213px; top: 34px; text-align: right; }
  .support-label { font-size: 13px; color: var(--ink); }
  .support-phone { display: flex; align-items: center; gap: 6px; font-size: 20px; color: #666; margin-top: 1px; }

  .hero { position: absolute; top: 97px; left: 0; width: 1200px; height: 492px; }
  .hero-bg { position: absolute; inset: 0; background: linear-gradient(100deg, #1f7d8a 0%, #27808c 45%, #1d6f7d 100%); }
  .hero-copy { position: absolute; left: 209px; top: 124px; width: 400px; color: var(--white); }
  .hero-kicker { font-family: "Raleway", Arial, sans-serif; font-size: 24px; font-weight: 400; }
  .hero-title { font-family: "Raleway", Arial, sans-serif; font-size: 29px; font-weight: 400; margin-top: 9px; }
  .hero-text { font-size: 11px; line-height: 17px; margin: 14px 0 0 3px; width: 392px; }
  .hero-actions { display: flex; gap: 10px; margin: 22px 0 0 2px; }
  .btn { display: inline-block; font-family: "Raleway", Arial, sans-serif; font-weight: 500; font-size: 15px; text-decoration: none; padding: 0 14px; line-height: 36px; height: 36px; }
  .btn-yellow { background: var(--yellow); color: #333; }
  .video-frame { position: absolute; left: 638px; top: 121px; width: 351px; height: 231px; background: var(--white); padding: 6px; }
  .video-still { width: 100%; height: 100%; background: radial-gradient(circle at 40% 35%, #d9a27a 0%, #7c4f69 45%, #3b2a44 100%); display: flex; align-items: center; justify-content: center; }
  .slider-dots { position: absolute; top: 463px; left: 587px; display: flex; gap: 3px; }
  .slider-dots span { width: 15px; height: 15px; border-radius: 50%; background: var(--white); }

  .content { position: absolute; top: 637px; left: 211px; width: 778px; display: flex; gap: 25px; }
  .side-nav { width: 177px; height: 191px; border: 1px solid var(--line); background: linear-gradient(#fdfdfd, #ececec); padding: 21px 0 0 28px; list-style: none; }
  .side-nav li { font-family: "Raleway", Arial, sans-serif; font-size: 12.5px; color: #444; height: 26.5px; display: flex; align-items: center; gap: 8px; }
  .side-nav li::before { content: ""; border-left: 4px solid #999; border-top: 3.5px solid transparent; border-bottom: 3.5px solid transparent; }
  .about { width: 560px; padding-top: 12px; }
  .about h1 { font-family: "Raleway", Arial, sans-serif; font-weight: 500; font-size: 21px; color: #333; margin-bottom: 11px; }
  .about p { font-size: 10.5px; line-height: 17px; color: var(--muted); margin-bottom: 9px; }
  .btn-teal { background: var(--teal); color: var(--white); margin-top: 4px; height: 36px; line-height: 36px; padding: 0 24px; font-size: 15px; }

  .site-footer { position: absolute; left: 0; top: 914px; width: 1200px; height: 66px; background: #000; color: var(--white); }
  .footer-legal { position: absolute; left: 210px; top: 25px; font-size: 10.5px; }
  .footer-social { position: absolute; right: 226px; top: 21px; display: flex; gap: 8px; }
  .footer-social span { width: 17px; height: 17px; border-radius: 50%; background: var(--white); }
</style>
</head>
<body>
  <header class="site-header">
    <div class="brand">
      <span class="brand-mark"></span>
      <div class="brand-text">
        <div class="brand-name">OAKLINE WEB STUDIO</div>
        <div class="brand-tagline">Websites built to perform</div>
      </div>
    </div>
    <div class="support">
      <div class="support-label">Phone Support</div>
      <div class="support-phone">
        <svg width="16" height="16" viewBox="0 0 24 24" aria-hidden="true"><path fill="#181818" d="M6.6 10.8a15.1 15.1 0 0 0 6.6 6.6l2.2-2.2c.3-.3.7-.4 1-.2 1.1.4 2.300.6 3.6.6.6 0 1 .4 1 1V20c0 .6-.4 1-1 1A17 17 0 0 1 3 4c0-.6.4-1 1-1h3.5c.6 0 1 .4 1 1 0 1.3.2 2.5.6 3.6.1.3 0 .7-.2 1z"/></svg>
        <span>555.014.2283</span>
      </div>
    </div>
  </header>

  <section class="hero">
    <div class="hero-bg" role="img" aria-label="Photo of a smiling team working together at a desk, tinted teal"></div>
    <div class="hero-copy">
      <h2 class="hero-kicker">Mauris vel lacus vitae felis</h2>
      <h1 class="hero-title">Vivamus porttitor purus nisi</h1>
      <p class="hero-text">Mauris vel lacus vitae felis vestibulum volutpat Etiam est nunc venenatis in tristique eu imperdiet ac nisl Cum sociis natoque penatibus et magnis dis parturient montes nascetur ridiculus mus In iaculis facilisis massa Etiam eu urna Sed porta Suspendisse quam leo molestie sed luctus quis feugiat Cras a ante vitae enim iaculis aliquam Mauris nunc quam</p>
      <div class="hero-actions">
        <a class="btn btn-yellow" href="#">Make an Appointment</a>
        <a class="btn btn-yellow" href="#">Call me back</a>
      </div>
    </div>
    <div class="video-frame">
      <div class="video-still" role="img" aria-label="Video still of a man using a tablet in a warmly lit office">
        <svg width="44" height="44" viewBox="0 0 44 44" aria-hidden="true"><circle cx="22" cy="22" r="22" fill="#fff"/><path d="M17 13 L31 22 L17 31 Z" fill="#111"/></svg>
      </div>
    </div>
    <div class="slider-dots"><span></span><span></span><span></span><span></span></div>
  </section>

  <main class="content">
    <ul class="side-nav">
      <li>About Us</li>
      <li>Services Provides</li>
      <li>Our Projects</li>
      <li>Support</li>
      <li>Blogs &amp; Articles</li>
      <li>Contact Us</li>
    </ul>
    <article class="about">
      <h1>ABOUT OUR COMPANY</h1>
      <p>Mauris vel lacus vitae felis vestibulum volutpat Etiam est nunc venenatis in tristique eu imperdiet ac nisl Cum sociis natoque penatibus et magnis dis parturient montes nascetur ridiculus mus In iaculis facilisis massa Etiam eu urna Sed porta Suspendisse quam leo molestie sed luctus quis feugiat in pede Fusce tellus</p>
      <p>Mauris vel lacus vitae felis vestibulum volutpat Etiam est nunc venenatis in tristique eu imperdiet ac nisl Cum sociis natoque penatibus et magnis dis parturient montes nascetur ridiculus mus In iaculis facilisis</p>
      <p>Cras a ante vitae enim iaculis aliquam Mauris nunc quam venenatis nec euismod sit amet egestas placerat est</p>
      <a class="btn btn-teal" href="#">Contact Us</a>
    </article>
  </main>

  <footer class="site-footer">
    <div class="footer-legal">© 2015 Company Name&nbsp; All right reserved&nbsp; Term of Use</div>
    <div class="footer-social" aria-label="Social links"><span></span><span></span><span></span><span></span></div>
  </footer>
</body>
</html>
```